Modern Label for cleaning products for the brand Vorlix

We need a label design for our line of cleaning products. The label should feature our logo and an image to identify the product's intended use. I've added our logo and an image for use. This only concerns the design of the label on the front of the bottle.

Label dimensions:
Label 1 (500ml bottle with spray): width 58mm x height 115mm
Label 2: (1L bottle): width 73mm x height 140mm
The design must be consistent for both bottles which you find in the pictures.

The bottles to be labeled are white. See the attachment for a photo of the bottles.

The photo must also appear on the label to identify the product's intended use.

Product information:
Brand: Vorlix
Product: Sanitary Cleaner

This text must be placed on the label:
"Cleans, descales & freshens. followed with this text: "Ideal for quick and powerful cleaning. A ready-to-use product for everyday use."

- Mention the seperate USP's: Sanitary, Bathroom, Toilet, Wet areas

Appearance: This is a consumer product, but it must have a professional appearance. We would like to see a design that use the color blue from our logo.

Target Market(s)

Consumers who take care of their homes and want to maintain it the correct (professional) way

Font styles to use
Sans Serif

Colors
0054AA
0677BA
7BADD7
CADEEF
E8F1F8

Requirements
Must have
• USP's + use of image and logo + blend in 1 design
Nice to have
• Keep the color of the logo in the design
Should not have
• Comic sans

```html
<!DOCTYPE html>
<html lang="en">
<head>
<meta charset="utf-8">
<title>Vorlix Sanitary Cleaner – Labels 500ml &amp; 1L</title>
<link href="https://fonts.googleapis.com/css2?family=Montserrat:ital,wght@0,700;1,800;1,900&family=Titillium+Web:wght@400;600;700&display=swap" rel="stylesheet">
<style>
  :root {
    --blue-logo: #0054AA;
    --blue-mid: #0677BA;
    --blue-soft: #7BADD7;
    --blue-pale: #CADEEF;
    --blue-mist: #E8F1F8;
    --blue-deep: #0B4391;
    --ink: #1c1c1c;
    --white: #ffffff;
    --canvas: #f3f5f8;
  }
  * { box-sizing: border-box; margin: 0; padding: 0; }
  html, body { width: 1109px; height: 1200px; overflow: hidden; }
  body {
    background: var(--canvas);
    display: flex;
    align-items: center;
    justify-content: center;
  }
  .label-row { display: flex; align-items: flex-end; gap: 60px; }

  .label {
    width: 33.6em;
    background: var(--white);
    border-radius: 1.2em;
    box-shadow: 0 6px 24px rgba(0, 40, 90, .12);
    display: flex;
    flex-direction: column;
    overflow: hidden;
  }
  .label--500 { font-size: 10px; height: 66.7em; }
  .label--1l { font-size: 12.6px; height: 64.4em; }

  /* Brand block */
  .brand {
    height: 16em;
    flex: none;
    display: flex;
    align-items: center;
    justify-content: center;
    gap: 1em;
  }
  .brand__dot {
    width: 3.2em; height: 3.2em;
    border-radius: 50%;
    background: var(--blue-logo);
  }
  .brand__name {
    font-family: "Montserrat", sans-serif;
    font-weight: 700;
    font-size: 3.6em;
    color: var(--ink);
    letter-spacing: -.01em;
  }

  /* Hero: band + photo */
  .hero { position: relative; flex: 1; overflow: hidden; }
  .hero__photo {
    position: absolute;
    inset: 8em 0 0 0;
    background: linear-gradient(160deg, var(--blue-soft) 0%, #9cc6e6 40%, var(--blue-pale) 80%, var(--blue-mist) 100%);
  }
  .hero__band {
    position: absolute;
    top: 0; left: 0; right: 0;
    height: 15em;
    background: linear-gradient(90deg, var(--blue-logo) 0%, var(--blue-mid) 100%);
    clip-path: polygon(0 30%, 100% 0, 100% 78%, 0 100%);
    display: flex;
    align-items: center;
    justify-content: center;
  }
  .product-title {
    font-family: "Montserrat", sans-serif;
    font-weight: 900;
    font-style: italic;
    font-size: 3.8em;
    line-height: .95;
    color: var(--white);
    text-transform: uppercase;
    transform: rotate(-6deg) translateY(.1em);
    text-shadow: 0 .06em 0 rgba(0, 40, 100, .45);
  }
  .product-title span { display: block; }
  .product-title span + span { padding-left: 1.1em; }

  .benefits {
    position: absolute;
    top: 6.8em; left: 1.6em;
    list-style: none;
    font-family: "Titillium Web", sans-serif;
    font-weight: 700;
    font-size: 2.2em;
    line-height: 1.25;
    color: var(--blue-logo);
  }
  .benefits li { display: flex; align-items: center; gap: .3em; }
  .tick {
    width: .8em; height: .8em;
    background: var(--white);
    border: .08em solid var(--ink);
    display: inline-flex;
    flex: none;
  }
  .tick svg { width: 100%; height: 100%; }

  .claim {
    position: absolute;
    left: 2.4em; right: 1.5em; bottom: 1em;
    font-family: "Montserrat", sans-serif;
    font-weight: 800;
    font-style: italic;
    font-size: 1.75em;
    line-height: 1.1;
    text-transform: uppercase;
    color: var(--white);
    letter-spacing: -.03em;
    text-shadow: 0 0 .12em var(--blue-logo), 0 0 .12em var(--blue-logo), .05em .05em 0 var(--blue-logo);
  }
  .claim span { display: block; }
  .claim span + span { padding-left: 3.4em; }

  /* Uses + footer */
  .panel {
    flex: none;
    background: var(--blue-deep);
    padding: 2em 2.4em 2.2em;
    color: var(--white);
    border-radius: 0 0 1.2em 1.2em;
  }
  .uses { display: flex; list-style: none; }
  .use {
    flex: 1;
    text-align: center;
    font-family: "Titillium Web", sans-serif;
    font-weight: 400;
  }
  .use + .use { border-left: .1em solid rgba(255, 255, 255, .7); }
  .use svg {
    width: 4.4em; height: 4.4em;
    fill: none; stroke: var(--white);
    stroke-width: 2; stroke-linejoin: round; stroke-linecap: round;
  }
  .use__name { display: block; font-size: 1.5em; margin-top: .3em; }

  .panel__foot {
    display: flex;
    align-items: flex-end;
    justify-content: space-between;
    margin-top: 2.6em;
    font-family: "Titillium Web", sans-serif;
  }
  .usage-note { font-size: 1.55em; line-height: 1.2; color: var(--blue-soft); }
  .volume { font-size: 2.5em; font-weight: 700; color: var(--blue-soft); line-height: 1; }
</style>
</head>
<body>
<div class="label-row">

  <article class="label label--500">
    <header class="brand">
      <span class="brand__dot"></span>
      <span class="brand__name">Vorlix</span>
    </header>
    <section class="hero">
      <div class="hero__photo" role="img" aria-label="Photo of a bright blue-tiled bathroom with a white toilet and glass shower"></div>
      <div class="hero__band">
        <h1 class="product-title"><span>Sanitary</span><span>Cleaner</span></h1>
      </div>
      <ul class="benefits">
        <li><span class="tick"><svg viewBox="0 0 10 10"><path d="M2 5l2 2 4-5" fill="none" stroke="#1c1c1c" stroke-width="1.6"/></svg></span>Cleans</li>
        <li><span class="tick"><svg viewBox="0 0 10 10"><path d="M2 5l2 2 4-5" fill="none" stroke="#1c1c1c" stroke-width="1.6"/></svg></span>Descales</li>
        <li><span class="tick"><svg viewBox="0 0 10 10"><path d="M2 5l2 2 4-5" fill="none" stroke="#1c1c1c" stroke-width="1.6"/></svg></span>Freshens</li>
      </ul>
      <p class="claim"><span>Ideal for quick and</span><span>powerful cleaning</span></p>
    </section>
    <footer class="panel">
      <ul class="uses">
        <li class="use"><svg viewBox="0 0 40 40"><path d="M20 14V8h5v3"/><path d="M6 14h28v3a14 9 0 0 1-28 0z"/><rect x="16" y="26" width="8" height="10"/></svg><span class="use__name">Sanitary</span></li>
        <li class="use"><svg viewBox="0 0 40 40"><path d="M10 20V8h4v3"/><path d="M4 20h32v4a8 8 0 0 1-8 8H12a8 8 0 0 1-8-8z"/><path d="M10 32l-1 3M30 32l1 3"/></svg><span class="use__name">Bathroom</span></li>
        <li class="use"><svg viewBox="0 0 40 40"><rect x="11" y="5" width="18" height="9" rx="2"/><path d="M9 17h22a11 8 0 0 1-22 0z"/><rect x="15" y="25" width="10" height="10"/></svg><span class="use__name">Toilet</span></li>
        <li class="use"><svg viewBox="0 0 40 40"><path d="M20 2v4"/><path d="M20 6c-8 0-10 8-10 15 0 8 4 14 10 14s10-6 10-14c0-7-2-15-10-15z"/><path d="M15 24h10"/></svg><span class="use__name">Wet areas</span></li>
      </ul>
      <div class="panel__foot">
        <p class="usage-note">A ready-to-use product<br>for everyday use</p>
        <p class="volume">500ml</p>
      </div>
    </footer>
  </article>

  <article class="label label--1l">
    <header class="brand">
      <span class="brand__dot"></span>
      <span class="brand__name">Vorlix</span>
    </header>
    <section class="hero">
      <div class="hero__photo" role="img" aria-label="Photo of a bright blue-tiled bathroom with a white toilet and glass shower"></div>
      <div class="hero__band">
        <h1 class="product-title"><span>Sanitary</span><span>Cleaner</span></h1>
      </div>
      <ul class="benefits">
        <li><span class="tick"><svg viewBox="0 0 10 10"><path d="M2 5l2 2 4-5" fill="none" stroke="#1c1c1c" stroke-width="1.6"/></svg></span>Cleans</li>
        <li><span class="tick"><svg viewBox="0 0 10 10"><path d="M2 5l2 2 4-5" fill="none" stroke="#1c1c1c" stroke-width="1.6"/></svg></span>Descales</li>
        <li><span class="tick"><svg viewBox="0 0 10 10"><path d="M2 5l2 2 4-5" fill="none" stroke="#1c1c1c" stroke-width="1.6"/></svg></span>Freshens</li>
      </ul>
      <p class="claim"><span>Ideal for quick and</span><span>powerful cleaning</span></p>
    </section>
    <footer class="panel">
      <ul class="uses">
        <li class="use"><svg viewBox="0 0 40 40"><path d="M20 14V8h5v3"/><path d="M6 14h28v3a14 9 0 0 1-28 0z"/><rect x="16" y="26" width="8" height="10"/></svg><span class="use__name">Sanitary</span></li>
        <li class="use"><svg viewBox="0 0 40 40"><path d="M10 20V8h4v3"/><path d="M4 20h32v4a8 8 0 0 1-8 8H12a8 8 0 0 1-8-8z"/><path d="M10 32l-1 3M30 32l1 3"/></svg><span class="use__name">Bathroom</span></li>
        <li class="use"><svg viewBox="0 0 40 40"><rect x="11" y="5" width="18" height="9" rx="2"/><path d="M9 17h22a11 8 0 0 1-22 0z"/><rect x="15" y="25" width="10" height="10"/></svg><span class="use__name">Toilet</span></li>
        <li class="use"><svg viewBox="0 0 40 40"><path d="M20 2v4"/><path d="M20 6c-8 0-10 8-10 15 0 8 4 14 10 14s10-6 10-14c0-7-2-15-10-15z"/><path d="M15 24h10"/></svg><span class="use__name">Wet areas</span></li>
      </ul>
      <div class="panel__foot">
        <p class="usage-note">A ready-to-use product<br>for everyday use</p>
        <p class="volume">1L</p>
      </div>
    </footer>
  </article>

</div>
</body>
</html>
```